Logo & Visitenkarte für Weinbauer
Zielgruppe
Ich bin Weinbauer und betreibe auch einen Buschenschank. Zielgruppe ist die Gastronomie und der (Durchschnitts-) Endverbraucher.
Aufgabenstellung
Unsere Betriebsstätte ist im Rebhügelgau Weinviertel (Österreich).
Wir wollen die Werte Tradition, Regional, Vertrauen und Bodenständigkeit vermitteln.
Unsere Kunden schätzen die Herkunft.
Das Logo soll als Firmenlogo und auch für die Weinetiketten verwendet werden können.

```html
<!DOCTYPE html>
<html lang="de">
<head>
<meta charset="utf-8">
<title>Weinbau Halder – Etikett</title>
<link rel="stylesheet" href="https://fonts.googleapis.com/css2?family=Open+Sans:wght@400&display=swap">
<style>
  :root {
    --backdrop: #d9d9d9;
    --label-black: #1c1c1c;
    --gold: #b38b5d;
    --fine-text: #8a8a8a;
  }
  html, body {
    margin: 0;
    padding: 0;
    width: 1200px;
    height: 960px;
    overflow: hidden;
    background: var(--backdrop);
    font-family: "Open Sans", Arial, sans-serif;
  }
  .canvas {
    position: relative;
    width: 1200px;
    height: 960px;
  }
  .neck-label {
    position: absolute;
    left: 510px;
    top: 110px;
    width: 180px;
    height: 120px;
    background: var(--label-black);
    display: flex;
    align-items: center;
    justify-content: center;
  }
  .neck-label .brand-dot {
    width: 56px;
    height: 56px;
  }
  .body-label {
    position: absolute;
    left: 300px;
    top: 300px;
    width: 600px;
    height: 520px;
    background: var(--label-black);
    display: flex;
    flex-direction: column;
    align-items: center;
    box-sizing: border-box;
    padding-top: 70px;
  }
  .brand-dot {
    display: block;
    border-radius: 50%;
    background: var(--gold);
  }
  .body-label .brand-dot {
    width: 130px;
    height: 130px;
  }
  .brand-name {
    margin: 34px 0 0;
    font-size: 50px;
    font-weight: 400;
    letter-spacing: 2px;
    color: var(--gold);
    line-height: 1;
  }
  .description {
    margin: 40px 0 0;
    width: 440px;
    font-size: 13px;
    line-height: 1.6;
    color: var(--fine-text);
    text-align: justify;
  }
</style>
</head>
<body>
  <main class="canvas">
    <section class="neck-label" aria-label="Halsetikett">
      <span class="brand-dot"></span>
    </section>
    <section class="body-label" aria-label="Hauptetikett">
      <span class="brand-dot"></span>
      <h1 class="brand-name">WEINBAUHALDER</h1>
      <p class="description">Handgelesene Trauben aus dem Rebhügelgau, gereift in kühlen Kellern. Ein ehrlicher Wein mit frischer Frucht, feiner Würze und klarer Herkunft. Passt zu Jause, Braten und guter Gesellschaft.</p>
    </section>
  </main>
</body>
</html>
```